Corporate Brochure Cover Design

We need a design for a corporate A4 Size portfolio cover (front and back) which we will be distributing. to our commercial clients.

We are a professional plumbing company that is an industry leader for service we provide to our clients and technology we use. The design needs to incorporate the colours black, red, white and silver and needs to include our logo. We dont have any slogans or mottos... If you wanted to use something it could be "Delivering exceptional service...Always!" however i dont want it to b the focal point of the cover.

Im looking for something professional and modern that has the WOW factor!

Size is A4 - both front and back covers. You can include pictures as well or sample pictures of where we can source and put our own team pictures.

if you have any questions, please do not hesitate to contact me.

Target Market(s)

Our commercial & strata clients - professional industry.

Industry/Entity Type

Commercial

Font styles to use
Sans Serif

Requirements
Must have
• Red, black, white, silver as the colour scheme.
• Include the logo.
Nice to have
• Modern design and something that makes the client go WOW before they open the brochure.
Should not have
• lots of text

```html
<!DOCTYPE html>
<html lang="en">
<head>
<meta charset="utf-8">
<title>Keystone – Brochure Cover</title>
<link href="https://fonts.googleapis.com/css2?family=Inter:wght@400;500;800&display=swap" rel="stylesheet">
<style>
  :root {
    --black: #231f20;
    --red: #c1202d;
    --white: #ffffff;
    --banner: #f2f2f4;
    --ink: #1e1e1e;
  }
  html, body {
    margin: 0;
    padding: 0;
    overflow: hidden;
    background: var(--black);
  }
  .cover {
    position: relative;
    width: 846px;
    height: 1200px;
    overflow: hidden;
    background: var(--black);
    font-family: "Inter", Arial, sans-serif;
  }
  .cover-art {
    position: absolute;
    inset: 0;
    width: 846px;
    height: 1200px;
  }
  .brand-name {
    position: absolute;
    left: 30px;
    top: 86px;
    margin: 0;
    font-weight: 800;
    font-size: 66px;
    letter-spacing: 1px;
    color: var(--white);
    line-height: 1;
  }
  .headline {
    position: absolute;
    left: 54px;
    top: 506px;
    margin: 0;
    font-weight: 400;
    font-size: 57px;
    line-height: 60px;
    letter-spacing: -0.5px;
    color: var(--ink);
  }
  .headline .accent {
    display: block;
    font-weight: 500;
    color: var(--red);
  }
  .web-address {
    position: absolute;
    left: 30px;
    top: 764px;
    margin: 0;
    font-weight: 500;
    font-size: 16px;
    color: var(--white);
  }
</style>
</head>
<body>
<main class="cover">
  <svg class="cover-art" viewBox="0 0 846 1200" xmlns="http://www.w3.org/2000/svg">
    <defs>
      <linearGradient id="plantroom-tone" x1="0" y1="0" x2="0.4" y2="1">
        <stop offset="0" stop-color="#8e8e8e"/>
        <stop offset="0.35" stop-color="#cfcfcf"/>
        <stop offset="0.7" stop-color="#bdbdbd"/>
        <stop offset="1" stop-color="#e6e6e6"/>
      </linearGradient>
    </defs>

    <polygon class="photo-area" role="img" aria-label="Photograph of a commercial plant room with white insulated pipework on steel supports over a polished grey floor"
             points="748,0 846,0 846,1200 148,1200" fill="url(#plantroom-tone)"/>

    <polygon class="accent-band" points="648,0 848,0 248,1200 48,1200" fill="var(--red)"/>

    <polygon class="title-banner" points="0,450 532,450 428,600 534,755 0,755" fill="var(--banner)"/>
  </svg>

  <h1 class="brand-name">KEYSTONE</h1>

  <h2 class="headline">PROVIDING<span class="accent">EFFECTIVE</span><span class="accent">SOLUTIONS</span></h2>

  <p class="web-address">www.keystoneplumbing.com.au</p>
</main>
</body>
</html>
```